I need an amazing business card!

I am the principle in my own software company that develops zorPad and mobile applications. I require a great business card design. I've attached my corporate logo (Thanks Tomas!).
I would like the design to integrate the logo, my name, email address and skype account:
name Brent Olafsen
email brentolafsen@tavrik.com
skype brentolafsen.net
I would like the back of the card to have a "write on me area" similar to the "write on me" card on this page, row 6:
http://us.prindlewick.com/design-templates/business-cards/#industry=Computing%20%26%20IT
As far as the rest - it's all you!
Updates
1) Please add an example telephone number as well.
Industry/Entity Type
Software
Look and feel
Each slider illustrates characteristics of the customer's brand and the style your logo design should communicate.

```html
<!DOCTYPE html>
<html lang="en">
<head>
<meta charset="utf-8">
<title>Tavrik Business Card – Brent Olafsen</title>
<link rel="stylesheet" href="https://fonts.googleapis.com/css2?family=Lato:ital,wght@0,300;0,400;0,700;1,400&display=swap">
<style>
  :root {
    --stage: #2f2f2f;
    --card-dark: #474747;
    --card-white: #ffffff;
    --lime: #8db63e;
    --ink: #4a4a4a;
    --rule: #9a9a9a;
    --text-light: #f2f2f2;
  }
  * { box-sizing: border-box; margin: 0; padding: 0; }
  html, body {
    width: 1200px; height: 926px; overflow: hidden;
    background: var(--stage);
    font-family: "Lato", Arial, sans-serif;
  }
  .stage {
    width: 1200px; height: 926px;
    display: flex; align-items: center; justify-content: center; gap: 40px;
  }
  .card {
    width: 540px; height: 309px; position: relative; overflow: hidden;
    border-radius: 3px;
    box-shadow: 0 14px 30px rgba(0,0,0,.45);
  }

  /* Front */
  .card--front { background: var(--card-dark); }
  .front__top {
    position: absolute; left: 0; top: 0; width: 100%; height: 142px;
    background: var(--card-white);
    display: flex; flex-direction: column; align-items: center; padding-top: 24px;
  }
  .brand-square {
    width: 66px; height: 66px; border-radius: 12px; background: var(--lime);
  }
  .brand-name {
    margin-top: 10px; font-size: 19px; font-weight: 400; color: var(--ink);
    letter-spacing: 9px; text-transform: lowercase; padding-left: 9px;
  }
  .front__stripe {
    position: absolute; left: 0; top: 142px; width: 100%; height: 8px; background: var(--lime);
  }
  .front__details {
    position: absolute; left: 0; top: 172px; width: 100%; text-align: center;
  }
  .person-name {
    font-size: 33px; color: var(--lime); font-weight: 300; letter-spacing: 1px;
    text-transform: uppercase;
  }
  .person-name strong { font-weight: 700; }
  .contact-list { list-style: none; margin-top: 12px; font-size: 18px; line-height: 1.35; color: var(--text-light); }
  .contact-label { color: var(--lime); font-style: italic; }

  /* Back */
  .card--back { background: var(--card-dark); }
  .back__brand {
    position: absolute; top: 20px; left: 0; width: 100%;
    display: flex; flex-direction: column; align-items: center;
  }
  .back__brand .brand-square { width: 48px; height: 48px; border-radius: 9px; background: var(--card-white); }
  .back__brand .brand-name { color: var(--card-white); font-size: 15px; letter-spacing: 7px; padding-left: 7px; margin-top: 7px; }
  .write-area {
    position: absolute; left: 34px; right: 34px; top: 120px; height: 158px;
    background: var(--card-white); padding: 24px 26px 0;
  }
  .write-area__line { height: 1px; background: var(--rule); margin-bottom: 36px; }
</style>
</head>
<body>
<main class="stage">
  <section class="card card--front" aria-label="Business card front">
    <div class="front__top">
      <div class="brand-square" aria-hidden="true"></div>
      <div class="brand-name">tavrik</div>
    </div>
    <div class="front__stripe"></div>
    <div class="front__details">
      <h1 class="person-name">Brent <strong>Olafsen</strong></h1>
      <ul class="contact-list">
        <li><span class="contact-label">email:</span> brentolafsen@tavrik.com</li>
        <li><span class="contact-label">skype:</span> brentolafsen.net</li>
      </ul>
    </div>
  </section>

  <section class="card card--back" aria-label="Business card back">
    <div class="back__brand">
      <div class="brand-square" aria-hidden="true"></div>
      <div class="brand-name">tavrik</div>
    </div>
    <div class="write-area" aria-label="Write-on area">
      <div class="write-area__line"></div>
      <div class="write-area__line"></div>
      <div class="write-area__line"></div>
    </div>
  </section>
</main>
</body>
</html>
```